Company Website for Varnoth Signal, an open source data analytics company focused on relationship and li

I need a company/brand website for our new startup, Varnoth Signal LLC. We are a company focused on using life pattern analysis techniques, looking at relationships and how relationships, attributes, and activity cluster to infer aggregate information about individuals and groups. Our focus is on improving the digital advertising market.

We have a company logo which I will upload shortly.

Target Market(s)

Digital Advertising

Number of Pages Required

3 page

Font styles to use
Sans Serif

Requirements
Must have
• An main page, about us, contact page.
Nice to have
• Varnoth Signal relies on state of the art analytics applied to a the digital marketing space. While it is heavy in science, we also understand the art of influence. The website should have a scientific edge but also a flair that illustrates our focus on applying the hard science and analytics to influencing the behavior of people.

```html
<!DOCTYPE html>
<html lang="en">
<head>
<meta charset="utf-8">
<title>Varnoth Signal</title>
<link rel="stylesheet" href="https://fonts.googleapis.com/css2?family=Montserrat:wght@400;500;600;700;800&family=Open+Sans:ital,wght@0,400;0,600;1,400&display=swap">
<style>
:root{
  --orange:#f58220;
  --blue:#1f8ad8;
  --blue-deep:#1766b5;
  --ink:#2a2a2a;
  --muted:#8a8a8a;
  --line:#d8d8d8;
  --soft:#f4f4f4;
  --dark:#1c1c26;
  --white:#ffffff;
}
*{box-sizing:border-box;margin:0;padding:0}
html,body{width:1200px;height:3871px;overflow:hidden;background:var(--white)}
body{position:relative;font-family:"Open Sans",Arial,sans-serif;color:var(--ink)}
.abs{position:absolute}
.head{font-family:"Montserrat",Arial,sans-serif}

/* header */
.site-header{left:0;top:0;width:1200px;height:111px;background:var(--white)}
.brand{left:98px;top:36px;font-family:"Montserrat",sans-serif;font-weight:800;font-size:26px;color:var(--blue);display:flex;align-items:center;gap:10px}
.brand-dot{width:14px;height:14px;border-radius:50%;background:var(--orange)}
.nav{left:322px;top:44px;display:flex;gap:34px;font-family:"Montserrat",sans-serif;font-size:14px;font-weight:500;color:var(--ink)}
.nav .active{color:var(--blue)}
.search{left:962px;top:44px}
.btn-signup{left:1000px;top:34px;width:100px;height:36px;border-radius:18px;background:var(--orange);color:#fff;font:600 13px "Montserrat",sans-serif;display:flex;align-items:center;justify-content:center}

/* hero */
.hero-art{left:0;top:111px;width:1200px;height:600px}
.hero-title{left:666px;top:262px;font:800 58px "Montserrat",sans-serif;color:var(--ink);letter-spacing:1px}
.hero-text{left:666px;top:350px;width:440px;font-size:14px;line-height:24px;color:#666}
.btn-orange{background:var(--orange);color:#fff;font:700 13px "Montserrat",sans-serif;display:flex;align-items:center;justify-content:center;border-radius:24px}
.hero-btn{left:666px;top:434px;width:142px;height:46px}
.dots{left:666px;top:522px;display:flex;gap:6px}
.dots span{width:12px;height:12px;border-radius:50%;border:2px solid #777}
.dots .on{border-color:var(--orange)}

/* section titles */
.sec-title{font:500 36px "Montserrat",sans-serif;color:var(--ink);display:flex;align-items:center;gap:14px}
.sec-title::before{content:"";width:32px;height:4px;background:var(--blue)}
.ghost{font:800 70px "Montserrat",sans-serif;color:#ececec;writing-mode:vertical-rl;transform:rotate(180deg);letter-spacing:4px}
.body-text{font-size:13px;line-height:34px;color:var(--muted)}

/* about */
.about-frame{left:591px;top:818px;width:493px;height:389px;border:2px solid #bbb}
.about-accent{left:937px;top:1117px;width:173px;height:116px;background:var(--orange)}
.about-img{left:606px;top:833px;width:493px;height:390px;background:radial-gradient(circle at 50% 45%,#7cc8ff 0%,#1f7ad0 45%,#0a2c6e 100%)}

/* services */
.services-bg{left:0;top:1321px;width:1200px;height:648px;background:var(--soft)}
.card{width:317px;height:356px;background:#fff;border:1px solid #e3e3e3;top:1507px}
.card-img{left:0;top:0;width:100%;height:165px}
.card-icon{left:138px;top:140px;width:42px;height:42px;transform:rotate(45deg);background:var(--orange);border:4px solid #fff;box-shadow:0 0 0 2px var(--orange)}
.card-title{left:0;top:226px;width:100%;text-align:center;font:600 16px "Montserrat",sans-serif;letter-spacing:.5px}
.card-text{left:30px;top:256px;width:257px;text-align:center;font-size:12px;line-height:22px;color:var(--muted)}
.card-link{left:0;top:312px;width:100%;text-align:center;font:700 11px "Montserrat",sans-serif;color:var(--orange)}
.sq{background:var(--orange);width:14px;height:14px}

/* testimonial */
.quote-band{left:0;top:1969px;width:1200px;height:271px;background:linear-gradient(90deg,#1a7fcf,#2a9be6)}
.avatar{left:128px;top:2061px;width:110px;height:110px;border-radius:50%;background:radial-gradient(circle,#c68a5c,#5a3a2a);border:4px solid #fff}
.avatar-badge{left:206px;top:2126px;width:34px;height:34px;border-radius:50%;background:var(--orange);color:#fff;font:700 22px Georgia,serif;display:flex;align-items:center;justify-content:center}
.quote{left:279px;top:2040px;width:815px;color:#fff;font-style:italic;font-size:14px;line-height:32px}
.quote-name{left:279px;top:2142px;color:#fff;font-size:14px}
.quote-name b{font-style:italic}

/* blog */
.post-title{font:500 26px "Montserrat",sans-serif;letter-spacing:.5px}
.post-rule{width:44px;height:4px;background:var(--blue)}
.btn-outline{border:2px solid var(--orange);color:var(--orange);border-radius:22px;font:700 12px "Montserrat",sans-serif;display:flex;align-items:center;justify-content:center;width:122px;height:40px}
.frame{border:2px solid #bbb}

/* footer */
.footer-art{left:0;top:3250px;width:1200px;height:621px}
.f-title{color:#fff}
.f-label{font:600 16px "Montserrat",sans-serif;color:#fff}
.field{background:#fff;border-radius:2px;font-size:11px;color:#555;padding:8px 8px}
.btn-submit{left:627px;top:3703px;width:75px;height:26px;font-size:11px}
.info{left:782px;color:#fff;font-size:13px;line-height:22px}
.info-icon{left:782px;width:36px;height:36px;border-radius:50%;border:2px solid #555;display:flex;align-items:center;justify-content:center}
.info-line{left:836px;color:#ddd;font-size:13px;line-height:20px}
.social{top:3702px;width:26px;height:26px;border-radius:50%}
.f-rule{left:98px;top:3793px;width:1004px;height:1px;background:#444}
.copy{left:0;top:3824px;width:1200px;text-align:center;color:#ccc;font-size:12px}
</style>
</head>
<body>

<header class="abs site-header">
  <div class="abs brand"><span class="brand-dot"></span>Varnoth Signal</div>
  <nav class="abs nav"><span class="active">HOME</span><span>ABOUT US</span><span>SERVICES</span><span>SOLUTIONS</span><span>BLOG</span><span>CONTACT US</span></nav>
  <svg class="abs search" width="14" height="14" viewBox="0 0 14 14"><circle cx="6" cy="6" r="4.5" fill="none" stroke="#1f8ad8" stroke-width="2"/><line x1="9.5" y1="9.5" x2="13" y2="13" stroke="#1f8ad8" stroke-width="2"/></svg>
  <div class="abs btn-signup">SIGN UP</div>
</header>

<svg class="abs hero-art" viewBox="0 0 1200 600" role="img" aria-label="Hero photo of a smiling woman with a phone surrounded by business strategy doodles">
  <defs><linearGradient id="heroG" x1="0" y1="0" x2="1" y2="0"><stop offset="0" stop-color="#d9d5cf"/><stop offset=".5" stop-color="#ecebe8"/><stop offset="1" stop-color="#f3f3f3"/></linearGradient></defs>
  <polygon points="0,0 1200,0 1200,431 929,599 0,495" fill="url(#heroG)"/>
  <polyline points="0,495 929,599 1200,431" fill="none" stroke="#1f8ad8" stroke-width="5"/>
</svg>
<div class="abs hero-title">Varnoth Signal</div>
<p class="abs hero-text">Sed ut perspiciatis unde omnis iste natus error sit voluptatem accusantium doloremque laudantium.</p>
<div class="abs btn-orange hero-btn">GET STARTED</div>
<div class="abs dots"><span></span><span></span><span class="on"></span><span></span><span></span></div>

<!-- about -->
<h2 class="abs sec-title" style="left:98px;top:844px">ABOUT US</h2>
<p class="abs body-text" style="left:98px;top:912px;width:470px">Sed ut perspiciatis unde omnis iste natus error sit voluptatem accusantium doloremque laudantium, totam rem aperiam, eaque ipsa quae ab illo inventore veritatis et quasi architecto beatae vitae dicta sunt explicabo. Nemo enim ipsam voluptatem quia voluptas sit aspernatur. Nemo enim ipsam voluptatem quia voluptas sit aspernatur aut odit aut fugit, sed quia consequuntur voluptatem sequi nesciunt.</p>
<div class="abs btn-orange" style="left:98px;top:1148px;width:122px;height:46px">READ MORE</div>
<div class="abs ghost" style="left:1118px;top:852px">ABOUT US</div>
<div class="abs about-frame"></div>
<div class="abs about-accent"></div>
<div class="abs about-img" role="img" aria-label="Blue network graphic of connected people figures under a magnifying glass"></div>

<!-- services -->
<div class="abs services-bg"></div>
<h2 class="abs sec-title" style="left:448px;top:1416px">OUR SERVICES</h2>
<div class="abs ghost" style="left:18px;top:1480px;color:#e6e6e6">SERVICES</div>
<div class="abs sq" style="left:78px;top:1820px"></div><div class="abs sq" style="left:70px;top:1846px;width:12px;height:12px"></div>
<div class="abs sq" style="left:1108px;top:1820px"></div><div class="abs sq" style="left:1100px;top:1846px;width:12px;height:12px"></div>

<div class="abs card" style="left:98px">
  <div class="abs card-img" role="img" aria-label="Photo of friends on a car at a beach sunset" style="background:linear-gradient(180deg,#f1b463,#9a6a3c 60%,#3d2c22)"></div>
  <div class="abs card-icon"></div>
  <div class="abs card-title">MAGNI DOLORES</div>
  <p class="abs card-text">Sed ut perspiciatis unde omnis iste natus error sit voluptatem accusan</p>
  <div class="abs card-link">READ MORE</div>
</div>
<div class="abs card" style="left:441px">
  <div class="abs card-img" role="img" aria-label="Photo of hands working on a laptop with charts" style="background:linear-gradient(160deg,#5a4a3a,#c9a07a 55%,#3a3028)"></div>
  <div class="abs card-icon"></div>
  <div class="abs card-title">RATIONE VOLUATEM</div>
  <p class="abs card-text">Sed ut perspiciatis unde omnis iste natus error sit voluptatem accusan</p>
  <div class="abs card-link">READ MORE</div>
</div>
<div class="abs card" style="left:784px">
  <div class="abs card-img" role="img" aria-label="Photo of colourful puzzle pieces on wood" style="background:linear-gradient(135deg,#6b3d2a,#8a5a3f 50%,#3e8f9a)"></div>
  <div class="abs card-icon"></div>
  <div class="abs card-title">ULLAM CORPORIS</div>
  <p class="abs card-text">Sed ut perspiciatis unde omnis iste natus error sit voluptatem accusan</p>
  <div class="abs card-link">READ MORE</div>
</div>

<!-- testimonial -->
<div class="abs quote-band"></div>
<svg class="abs" style="left:20px;top:2110px" width="70" height="60" viewBox="0 0 70 60"><g fill="#fff" opacity=".5"><rect x="10" y="10" width="14" height="14" transform="rotate(20 17 17)"/><rect x="34" y="20" width="12" height="12" transform="rotate(20 40 26)"/><rect x="14" y="36" width="12" height="12" transform="rotate(20 20 42)"/></g></svg>
<svg class="abs" style="left:1080px;top:2110px" width="70" height="60" viewBox="0 0 70 60"><g fill="#fff" opacity=".5"><rect x="30" y="6" width="14" height="14" transform="rotate(20 37 13)"/><rect x="10" y="24" width="12" height="12" transform="rotate(20 16 30)"/><rect x="40" y="34" width="12" height="12" transform="rotate(20 46 40)"/></g></svg>
<div class="abs avatar" role="img" aria-label="Portrait photo of a customer"></div>
<div class="abs avatar-badge">&rdquo;</div>
<p class="abs quote">" Sed ut perspiciatis unde omnis iste natus error sit voluptatem accusantium doloremque laudantium, totam rem aperiam, eaque ipsa quae ab illo inventore veritatis et quasi architecto beatae vitae dicta sunt explicabo. Nemo enim ipsam voluptatem quia voluptas sit aspernatur aut odit aut fugit, sed quia consequuntur magni dolores "</p>
<div class="abs quote-name"><b style="font-style:normal">- Mara Lindqvist</b> , <i>Customer</i></div>

<!-- blog -->
<h2 class="abs sec-title" style="left:470px;top:2338px">BLOG POSTS</h2>
<div class="abs ghost" style="left:1118px;top:2330px">BLOG POSTS</div>

<div class="abs" style="left:160px;top:2680px;width:230px;height:82px;background:var(--blue)"></div>
<div class="abs frame" style="left:139px;top:2477px;width:320px;height:271px"></div>
<div class="abs" role="img" aria-label="Photo of a woman at a laptop beneath a drawn lightbulb and business icons" style="left:178px;top:2497px;width:320px;height:253px;background:linear-gradient(180deg,#e9e2d2,#f3c65a 35%,#e8e4dc 70%,#c7b79c)"></div>
<div class="abs sq" style="left:140px;top:2752px"></div><div class="abs sq" style="left:176px;top:2772px"></div><div class="abs sq" style="left:150px;top:2782px"></div>
<h3 class="abs post-title" style="left:593px;top:2494px">UM QUIA DOLOR SITAM</h3>
<div class="abs post-rule" style="left:593px;top:2541px"></div>
<p class="abs body-text" style="left:593px;top:2568px;width:480px">Sed ut perspiciatis unde omnis iste natus error sit voluptatem accusantium doloremque laudantium, totam rem aperiam, eaque ipsa quae ab illo inventore veritatis et quas arch dicta sunt explicabo.</p>
<div class="abs btn-outline" style="left:593px;top:2699px">READ MORE</div>

<h3 class="abs post-title" style="left:139px;top:2889px">UM QUIA DOLOR SITAM</h3>
<div class="abs post-rule" style="left:139px;top:2936px"></div>
<p class="abs body-text" style="left:139px;top:2962px;width:480px">Sed ut perspiciatis unde omnis iste natus error sit voluptatem accusantium doloremque laudantium, totam rem aperiam, eaque ipsa quae ab illo inventore veritatis et quas arch dicta sunt explicabo.</p>
<div class="abs btn-outline" style="left:139px;top:3094px">READ MORE</div>
<div class="abs frame" style="left:743px;top:2869px;width:317px;height:240px"></div>
<div class="abs" style="left:808px;top:3032px;width:228px;height:121px;background:var(--blue)"></div>
<div class="abs" role="img" aria-label="Photo of hands holding a coffee cup and a tablet" style="left:702px;top:2890px;width:322px;height:253px;background:linear-gradient(135deg,#3a2a22,#a98a70 50%,#e4e0da)"></div>
<div class="abs sq" style="left:1008px;top:3158px"></div><div class="abs sq" style="left:1032px;top:3170px"></div><div class="abs sq" style="left:1040px;top:3146px;width:12px;height:12px"></div>

<!-- footer -->
<svg class="abs footer-art" viewBox="0 0 1200 621" aria-hidden="true">
  <polygon points="0,182 490,14 1200,104 1200,621 0,621" fill="#1c1c26"/>
  <polyline points="0,182 490,14 1200,104" fill="none" stroke="#1f8ad8" stroke-width="6"/>
</svg>
<h2 class="abs sec-title f-title" style="left:466px;top:3396px">CONTACT US</h2>
<div class="abs f-label" style="left:98px;top:3488px">Get In Touch:</div>
<div class="abs field" style="left:98px;top:3532px;width:297px;height:31px">NAME :</div>
<div class="abs field" style="left:408px;top:3532px;width:294px;height:31px">PHONE :</div>
<div class="abs field" style="left:98px;top:3576px;width:604px;height:31px">EMAIL :</div>
<div class="abs field" style="left:98px;top:3620px;width:604px;height:70px">MESSAGE :</div>
<div class="abs btn-orange btn-submit">SUBMIT</div>

<div class="abs f-label" style="left:782px;top:3488px">Contact Information</div>
<div class="abs info-icon" style="top:3530px"><svg width="14" height="16" viewBox="0 0 14 16"><path d="M7 1a5 5 0 0 1 5 5c0 4-5 9-5 9S2 10 2 6a5 5 0 0 1 5-5z" fill="#f58220"/><circle cx="7" cy="6" r="2" fill="#1c1c26"/></svg></div>
<div class="abs info-line" style="top:3530px">: Varnoth Signal.<br>: 135,Qui ratione voluptatem sequi.</div>
<div class="abs info-icon" style="top:3589px"><svg width="14" height="14" viewBox="0 0 14 14"><path d="M3 1l2 3-1.5 1.5a8 8 0 0 0 5 5L10 9l3 2-1 2.5C6 13 1 8 .5 2z" fill="#f58220"/></svg></div>
<div class="abs info-line" style="top:3597px">: Phone : 1 555 014 2290</div>
<div class="abs info-icon" style="top:3641px"><svg width="16" height="12" viewBox="0 0 16 12"><rect x="1" y="1" width="14" height="10" fill="#f58220"/><polyline points="1,1 8,7 15,1" fill="none" stroke="#1c1c26" stroke-width="1.5"/></svg></div>
<div class="abs info-line" style="top:3649px">: Email : hello@varnothsignal.com</div>
<div class="abs social" style="left:786px;background:#2f5fb3"></div>
<div class="abs social" style="left:820px;background:#2aa3ef"></div>
<div class="abs social" style="left:854px;background:#d33a2c"></div>
<div class="abs social" style="left:888px;background:#c79a5a"></div>

<div class="abs f-rule"></div>
<div class="abs copy">Copyrights © 2018, Varnoth Signal, All Rights Reserved.Privacy policy</div>

</body>
</html>
```